New Business Card for Web Design/Internet Marketing Company

Looking for a great looking new business card. We are a 10 year old web design, internet marketing and website management company that works mostly with small businesses.

Our new card needs to better match the colors and style of our website, be bold, extremely usable and slightly edgy.

Target Market(s)

Small/Medium businesses that have websites

Industry/Entity Type

Internet

Requirements
Must have
• Front and back design, full color, rounded corners please

Must use the colors/style of our website (JPG provided)

INFO FOR CARDS (as readable as possible please)
Mark Lenner
President/CEO
mark@trelvanmedia.example
Phone: 520-381-7459
Toll Free: 866-381-7459
Address: 4315 W. Calloway Ave. Ste. 140, Tucson, AZ 85792

THINGS I WANT TO PROMOTE (if there is room):
1. Our Website - www.trelvanmedia.example

2. Social Media
Twitter: @trelvanmedia
Facebook: www.facebook.com/trelvanmedia

3. Our Services
Web Design
Internet Marketing
Website Management

```html
<!DOCTYPE html>
<html lang="en">
<head>
<meta charset="utf-8">
<title>Trelvan Media — Business Card</title>
<link rel="stylesheet" href="https://fonts.googleapis.com/css2?family=Source+Sans+3:wght@400;600;700&display=swap">
<style>
  :root {
    --orange: #f0852d;
    --blue: #1a8dc6;
    --ink: #4a4a4a;
    --muted: #6b6b6b;
    --paper: #ffffff;
    --backdrop: #e9e6e2;
    --rule: #c9c9c9;
  }
  * { box-sizing: border-box; margin: 0; padding: 0; }
  html, body { width: 1200px; height: 758px; overflow: hidden; }
  body {
    background: var(--backdrop);
    font-family: "Source Sans 3", "Myriad Pro", Arial, sans-serif;
    color: var(--ink);
    position: relative;
  }
  .card {
    position: absolute;
    top: 219px;
    width: 540px;
    height: 320px;
    background: var(--paper);
    border-radius: 28px;
    overflow: hidden;
    box-shadow: 0 6px 18px rgba(0,0,0,0.18);
  }
  .card--front { left: 40px; }
  .card--back { left: 620px; }

  /* Front */
  .front-wave { position: absolute; inset: 0; width: 100%; height: 100%; }
  .brand-front {
    position: absolute;
    left: 40px; top: 96px;
    width: 210px;
    display: flex; align-items: center; gap: 10px;
  }
  .brand-dot {
    width: 22px; height: 22px; border-radius: 50%;
    background: var(--blue); flex: none;
  }
  .brand-name {
    font-weight: 700; color: var(--orange);
    font-size: 32px; line-height: 1; letter-spacing: -0.5px;
  }
  .divider {
    position: absolute; left: 272px; top: 44px;
    width: 2px; height: 150px; background: var(--rule);
  }
  .contact { position: absolute; left: 292px; top: 40px; }
  .contact__name { color: var(--orange); font-weight: 700; font-size: 21px; line-height: 1.1; }
  .contact__role { font-size: 16px; color: var(--ink); margin-bottom: 14px; }
  .contact__list { list-style: none; }
  .contact__item {
    display: flex; align-items: center; gap: 8px;
    font-size: 14px; line-height: 20px; color: var(--muted);
  }
  .contact__item svg { width: 12px; height: 12px; flex: none; }
  .address {
    position: absolute; left: 40px; bottom: 28px;
    color: var(--paper); font-size: 15px; line-height: 20px;
  }

  /* Back */
  .brand-back {
    position: absolute; left: 40px; top: 118px;
    display: flex; align-items: center; gap: 12px;
  }
  .brand-back .brand-dot { width: 30px; height: 30px; }
  .brand-back .brand-name { font-size: 44px; }
  .services { position: absolute; left: 300px; top: 46px; }
  .services__title { color: var(--orange); font-weight: 700; font-size: 28px; margin-bottom: 8px; }
  .services__list { list-style: none; }
  .services__item {
    font-size: 24px; line-height: 30px; color: var(--ink);
    display: flex; align-items: center; gap: 8px;
  }
  .services__item::before {
    content: ""; width: 7px; height: 7px; border-radius: 50%;
    background: var(--orange); flex: none;
  }
  .social { position: absolute; left: 300px; top: 214px; list-style: none; }
  .social__item {
    display: flex; align-items: center; gap: 8px;
    font-size: 15px; line-height: 22px; color: var(--muted);
  }
  .social__mark { width: 12px; height: 12px; background: var(--blue); border-radius: 2px; flex: none; }
</style>
</head>
<body>

<section class="card card--front" aria-label="Business card front">
  <svg class="front-wave" viewBox="0 0 540 320" preserveAspectRatio="none" aria-hidden="true">
    <path d="M0 238 C120 180 260 250 380 238 C460 230 510 200 540 172 L540 190 C505 222 455 246 380 254 C260 266 120 200 0 256 Z" fill="var(--blue)"/>
    <path d="M0 262 C120 206 260 272 380 260 C460 252 510 224 540 196 L540 320 L0 320 Z" fill="var(--orange)"/>
  </svg>

  <div class="brand-front">
    <span class="brand-dot" aria-hidden="true"></span>
    <span class="brand-name">Trelvan Media</span>
  </div>

  <div class="divider" aria-hidden="true"></div>

  <div class="contact">
    <p class="contact__name">Mark Lenner</p>
    <p class="contact__role">President/CEO</p>
    <ul class="contact__list">
      <li class="contact__item">
        <svg viewBox="0 0 12 12" aria-hidden="true"><circle cx="6" cy="6" r="5.3" fill="none" stroke="currentColor"/><path d="M4 3.2 L5.2 3.2 L5.4 4.8 L4.8 5.3 C5.2 6.2 5.8 6.8 6.7 7.2 L7.2 6.6 L8.8 6.8 L8.8 8 C6 8.3 3.7 6 4 3.2 Z" fill="currentColor"/></svg>
        866-381-7459
      </li>
      <li class="contact__item">
        <svg viewBox="0 0 12 12" aria-hidden="true"><circle cx="6" cy="6" r="5.3" fill="none" stroke="currentColor"/><path d="M4 3.2 L5.2 3.2 L5.4 4.8 L4.8 5.3 C5.2 6.2 5.8 6.8 6.7 7.2 L7.2 6.6 L8.8 6.8 L8.8 8 C6 8.3 3.7 6 4 3.2 Z" fill="currentColor"/></svg>
        520-381-7459
      </li>
      <li class="contact__item">
        <svg viewBox="0 0 12 12" aria-hidden="true"><rect x="1" y="3" width="10" height="7" rx="1" fill="currentColor"/><path d="M1.5 3.5 L6 7 L10.5 3.5" fill="none" stroke="#fff"/></svg>
        mark@trelvanmedia.example
      </li>
      <li class="contact__item">
        <svg viewBox="0 0 12 12" aria-hidden="true"><circle cx="6" cy="6" r="5" fill="currentColor"/><path d="M1 6 H11 M6 1 C3.5 3.5 3.5 8.5 6 11 M6 1 C8.5 3.5 8.5 8.5 6 11" fill="none" stroke="#fff" stroke-width="0.7"/></svg>
        www.trelvanmedia.example
      </li>
    </ul>
  </div>

  <address class="address" style="font-style:normal">
    4315 W. Calloway Ave. Ste. 140<br>
    Tucson, AZ 85792
  </address>
</section>

<section class="card card--back" aria-label="Business card back">
  <div class="brand-back">
    <span class="brand-dot" aria-hidden="true"></span>
    <span class="brand-name">Trelvan</span>
  </div>

  <div class="services">
    <h2 class="services__title">Our Services</h2>
    <ul class="services__list">
      <li class="services__item">Web Design</li>
      <li class="services__item">Internet Marketing</li>
      <li class="services__item">Website Management</li>
    </ul>
  </div>

  <ul class="social">
    <li class="social__item"><span class="social__mark" aria-hidden="true"></span>@trelvanmedia</li>
    <li class="social__item"><span class="social__mark" aria-hidden="true"></span>trelvanmedia</li>
  </ul>
</section>

</body>
</html>
```